Stationery Project with Logo Design

We need stationery & logo design for a new small boutique marketing company based in Perth Western Australia. The company is called Blue Lantern Marketing.

We offer marketing services to small-to-medium business.

We would like to see designs strong & innovative designs and should use red as one of the colours.

The final design should communicate innovation and fun.

Target Market(s)

Small to medium business owners between 20 - 50 years

Industry/Entity Type

Business

Logo Text

```html
<!DOCTYPE html>
<html lang="en">
<head>
<meta charset="UTF-8">
<title>Blue Lantern Marketing – Business Card</title>
<link href="https://fonts.googleapis.com/css2?family=Montserrat:wght@700&family=Questrial&display=swap" rel="stylesheet">
<style>
  :root {
    --brand-red: #b3222a;
    --ink-grey: #5c5c5c;
    --paper-white: #fbfbfa;
    --backdrop: #e9e9e7;
    --logo-white: #ffffff;
  }
  * { margin: 0; padding: 0; box-sizing: border-box; }
  html, body {
    width: 1200px; height: 800px; overflow: hidden;
    background: var(--backdrop);
  }
  .stationery {
    width: 1200px; height: 800px;
    display: flex; align-items: center; justify-content: center; gap: 40px;
  }
  .card {
    position: relative;
    width: 540px; height: 309px;
    box-shadow: 0 10px 28px rgba(0,0,0,0.16);
    font-family: "Questrial", sans-serif;
  }
  .card--front { background: var(--paper-white); }
  .card--back {
    background: var(--brand-red);
    display: flex; align-items: center; justify-content: center;
  }
  .wordmark {
    font-family: "Questrial", sans-serif;
    text-transform: uppercase;
    line-height: 1.05;
    text-align: right;
  }
  .card--front .wordmark {
    position: absolute; top: 40px; right: 36px;
    color: var(--brand-red);
    font-size: 30px; letter-spacing: 0.5px;
  }
  .wordmark__sub {
    display: block; font-size: 0.5em; letter-spacing: 4px;
  }
  .card--back .wordmark {
    color: var(--logo-white);
    font-size: 40px; letter-spacing: 0.5px;
  }
  .holder {
    position: absolute; left: 34px; top: 160px;
    color: var(--ink-grey);
  }
  .holder__name {
    font-family: "Montserrat", sans-serif; font-weight: 700;
    font-size: 15px; letter-spacing: 0.5px; text-transform: uppercase;
  }
  .holder__role { font-size: 12px; margin-top: 2px; }
  .contact-list {
    list-style: none; margin-top: 18px;
  }
  .contact-list li {
    display: flex; align-items: center; gap: 10px;
    font-size: 14px; line-height: 1; margin-bottom: 7px;
  }
  .contact-icon { width: 16px; height: 16px; flex: none; }
</style>
</head>
<body>
<main class="stationery">
  <section class="card card--front" aria-label="Business card front">
    <div class="wordmark">Blue Lantern<span class="wordmark__sub">Marketing</span></div>
    <div class="holder">
      <p class="holder__name">Dana Whitford</p>
      <p class="holder__role">Founder &amp; CEO</p>
      <ul class="contact-list">
        <li>
          <svg class="contact-icon" viewBox="0 0 16 16" aria-hidden="true">
            <circle cx="8" cy="8" r="8" fill="#b3222a"/>
            <path d="M5.2 4.2l1.5-.4.9 2-1 .8c.5 1.1 1.3 1.9 2.4 2.4l.8-1 2 .9-.4 1.5c-3.3.3-6.5-2.9-6.2-6.2z" fill="#fff"/>
          </svg>
          (555) 014-2087
        </li>
        <li>
          <svg class="contact-icon" viewBox="0 0 16 16" aria-hidden="true">
            <circle cx="8" cy="8" r="8" fill="#b3222a"/>
          </svg>
          bluelantern.chat
        </li>
        <li>
          <svg class="contact-icon" viewBox="0 0 16 16" aria-hidden="true">
            <circle cx="8" cy="8" r="8" fill="#b3222a"/>
            <rect x="4" y="5.3" width="8" height="5.6" fill="none" stroke="#fff" stroke-width="1"/>
            <path d="M4 5.3l4 3 4-3" fill="none" stroke="#fff" stroke-width="1"/>
          </svg>
          info@bluelantern.com
        </li>
        <li>
          <svg class="contact-icon" viewBox="0 0 16 16" aria-hidden="true">
            <circle cx="8" cy="8" r="8" fill="#b3222a"/>
            <circle cx="8" cy="8" r="4.5" fill="none" stroke="#fff" stroke-width="0.9"/>
            <ellipse cx="8" cy="8" rx="2" ry="4.5" fill="none" stroke="#fff" stroke-width="0.9"/>
            <path d="M3.5 8h9" stroke="#fff" stroke-width="0.9"/>
          </svg>
          www.bluelantern.com
        </li>
      </ul>
    </div>
  </section>

  <section class="card card--back" aria-label="Business card back">
    <div class="wordmark">Blue Lantern<span class="wordmark__sub">Marketing</span></div>
  </section>
</main>
</body>
</html>
```